Need Business Card for our Real Estate Business with Sales Executive's Picture

PANTONE 484 C ( RED)

PANTONE 2766 C ( BLUE

Industry/Entity Type

Real Estate

Contact Information for Business Card

Name, Mobile, email, & picture of Person
Agency Phone, address, Web address

Requirements
Must have
• Our Logo Colours, Agent Picture,

```html
<!DOCTYPE html>
<html lang="en">
<head>
<meta charset="utf-8">
<title>Dunmore Real Estate – Business Card</title>
<link rel="stylesheet" href="https://fonts.googleapis.com/css2?family=Open+Sans:wght@400;600&display=swap">
<style>
  :root {
    --backdrop: #c9cbcf;
    --card: #ffffff;
    --navy: #04153a;
    --ink: #444444;
    --ink-soft: #555555;
    --photo-top: #3c63a8;
    --photo-bottom: #14316e;
    --white: #ffffff;
  }
  * { margin: 0; padding: 0; box-sizing: border-box; }
  html, body {
    width: 1200px; height: 1000px; overflow: hidden;
    background: var(--backdrop);
    font-family: "Open Sans", Arial, sans-serif;
  }
  .card {
    position: absolute; left: 261px; width: 681px; height: 388px;
    background: var(--card);
  }
  .card--front { top: 85px; }
  .card--back { top: 525px; }

  .brand-name {
    position: absolute; left: 0; width: 100%;
    text-align: center; font-weight: 600; letter-spacing: 2px;
  }
  .card--front .brand-name { top: 56px; font-size: 22px; color: var(--navy); }

  .agent-photo {
    position: absolute; left: 31px; top: 40px; width: 125px; height: 158px;
    background: linear-gradient(180deg, var(--photo-top), var(--photo-bottom));
  }
  .agent-name {
    position: absolute; left: 185px; top: 118px;
    font-size: 25px; color: var(--ink); font-weight: 400;
  }
  .agent-title {
    position: absolute; left: 185px; top: 151px;
    font-size: 19px; color: var(--ink);
  }
  .address-band { position: absolute; left: 0; top: 0; }

  .contact-list {
    position: absolute; left: 210px; top: 266px; list-style: none;
  }
  .contact-list li {
    display: flex; align-items: center; height: 31.5px;
    font-size: 19.5px; color: var(--ink-soft);
  }
  .contact-list svg { width: 18px; height: 18px; margin-right: 23px; flex: none; }

  .back-panel {
    position: absolute; left: 48px; top: 47px; width: 584px; height: 292px;
    background: var(--navy);
    display: flex; align-items: center; justify-content: center;
  }
  .back-panel .brand-name {
    position: static; color: var(--white); font-size: 40px; letter-spacing: 4px;
    font-weight: 400;
  }
</style>
</head>
<body>

<section class="card card--front">
  <div class="brand-name">DUNMORE</div>

  <div class="agent-photo" role="img" aria-label="Portrait photo of the sales executive"></div>
  <h1 class="agent-name">Name of Sales Executive's</h1>
  <p class="agent-title">Sales Executive</p>

  <svg class="address-band" width="681" height="260" viewBox="0 0 681 260" aria-hidden="false">
    <rect x="0" y="205" width="681" height="2.5" fill="var(--navy)"/>
    <path d="M50 206 H632 C620 210 612 236 600 246 Q592 252 580 252 H102 Q90 252 82 246 C70 236 62 210 50 206 Z" fill="var(--navy)"/>
    <text x="341" y="234" text-anchor="middle" fill="var(--white)" font-family="Open Sans, Arial, sans-serif" font-size="19.5">address of Dunmore Real Estate</text>
  </svg>

  <ul class="contact-list">
    <li>
      <svg viewBox="0 0 18 18" fill="none" stroke="var(--ink-soft)" stroke-width="1.4">
        <circle cx="9" cy="9" r="7.5"/>
        <path d="M6.3 5.2 L7.6 7 L6.9 7.9 Q7.8 9.9 10 11 L10.9 10.3 L12.7 11.6 Q12 13 10.8 12.9 Q6.4 12 5.1 7.3 Q5 6 6.3 5.2 Z" fill="var(--ink-soft)" stroke="none"/>
      </svg>
      mobile / agency phone
    </li>
    <li>
      <svg viewBox="0 0 18 18">
        <rect x="1.5" y="4" width="15" height="10.5" fill="var(--ink-soft)"/>
        <path d="M1.5 4.5 L9 10 L16.5 4.5" fill="none" stroke="var(--white)" stroke-width="1.2"/>
      </svg>
      dunmore@email.com
    </li>
    <li>
      <svg viewBox="0 0 18 18" fill="none" stroke="var(--ink-soft)" stroke-width="1.3">
        <circle cx="9" cy="9" r="7.5"/>
        <ellipse cx="9" cy="9" rx="3.3" ry="7.5"/>
        <path d="M1.5 9 H16.5 M2.8 5 H15.2 M2.8 13 H15.2"/>
      </svg>
      www.web address.com
    </li>
  </ul>
</section>

<section class="card card--back">
  <div class="back-panel">
    <div class="brand-name">DUNMORE</div>
  </div>
</section>

</body>
</html>
```